Webpage for co-working space for tech startups

We have an established co-working space in Aalborg Denmark where we have around 30 companies sharing office space. We are starting a new chapter for us and would like to have a new graphical image - new logo and new webpage, but keep the same name. The webpage should be professional, but also "fun", not too serious. We are all about working hard on our companies, but also taking some time off in between and being social and having fun. We are not corporate, but want to project the image that we are serious about what we do.

We currently have a black/red logo (see www.hivedesk.dk or test.hivedesk.dk), but are interesting in having a new logo design, so colour can be chosen freely. Currently our logo is a big HIVE and a little desk underneath the HIVE. The new logo will be one word "hivedesk" with a small logo before or on top.

If we can make a good webpage for this project, then I have a second more simple project which is also a small single page wordpress site which I would also like to have made.

Target Market(s)

tech startups - relatively new companies, typically younger people 20-35 with a tech background - business or programming, preferably both

Industry/Entity Type

HIVE

Logo Text

hivedesk

Coding

Coded - Design and coding required

Number of Pages Required

4 page

Font styles to use
Sans Serif

Colors

Designer to choose colors to be used in the design.

Requirements
Must have
• Wordpress CMS.
• Mobile and PC optimized
• 2 languages - English and Danish
• Four sections, could be four pages, or four sections of a single page.
• "Home", "Residents", "Our Working Space", "Our Event Space"
• Footer of page or pages should have contact information.
• "Home" has some information about who we are and what we do
• "Residents" has a list of all our residents - it should be possible to easily add and removed new / old residents - See one example here: http://test.hivedesk.dk/en_GB/beboere/ or another example here: http://www.hivedesk.dk/beboere/ - one of our colleagues http://pilotbarn.dk/startups/ or another one of our colleagues http://www.brightkelpyard.dk/residents/
• "Our working space" will have a description of our building, a map of where it is and a bunch of photos which show the different offices, meeting rooms and people working
• "Our events space" will have a description of our event spaces, details of cost + different arrangments of furniture, and lots of photos of events, see here for an example http://www.hivedesk.dk/lej-vores-lokaler/
• Our current webpage - www.hivedesk.dk was put together very quickly and has not really been optimized. We started a new webpage test.hivedesk.dk, but it was never really finished.
• We are looking for a simple webpage, not too much going on. Examples of some of our colleagues in the business http://pilotbarn.dk/, http://www.brightkelpyard.dk/,
Nice to have
• http://www.brightkelpyard.dk/ is a really good template for us. If we can get something like this, we are happy.

```html
<!DOCTYPE html>
<html lang="en">
<head>
<meta charset="utf-8">
<title>hivedesk – co-working space</title>
<link rel="stylesheet" href="https://fonts.googleapis.com/css2?family=Oswald:wght@400;500;700&family=Work+Sans:wght@400;600;700&family=Open+Sans:wght@400;600;700&display=swap">
<style>
:root{
  --red:#c4161c;
  --red-dark:#a90f15;
  --ink:#1d1d1d;
  --text:#3a3a3a;
  --light:#f1f1f1;
  --white:#ffffff;
  --dark:#2b2b2b;
}
*{margin:0;padding:0;box-sizing:border-box}
html,body{width:1200px;height:3163px;overflow:hidden}
body{position:relative;background:var(--white);font-family:"Open Sans",sans-serif;color:var(--text)}
.abs{position:absolute}

/* Hero */
.hero{left:0;top:0;width:1200px;height:690px;background:linear-gradient(180deg,#3a3c3e 0%,#55585a 45%,#2f3032 100%);overflow:hidden}
.hero-shade{inset:0;background:rgba(0,0,0,.25)}
.brand{left:108px;top:48px;font-family:"Oswald",sans-serif;font-weight:700;font-size:36px;color:var(--white);letter-spacing:.5px}
.nav{left:450px;top:58px;display:flex;gap:18px;font-family:"Oswald",sans-serif;font-size:16px;color:var(--white);text-transform:uppercase;white-space:nowrap}
.lang{left:995px;top:56px;width:88px;height:32px;border:1.5px solid var(--white);border-radius:3px;color:var(--white);font-family:"Oswald",sans-serif;font-size:13px;display:flex;align-items:center;justify-content:center;gap:6px}
.hero-title{left:0;width:1200px;top:262px;text-align:center;font-family:"Work Sans",sans-serif;font-weight:600;font-size:96px;line-height:110px;color:var(--white);letter-spacing:4px}
.btn-quote{left:515px;top:428px;width:170px;height:38px;background:var(--red);color:var(--white);font-family:"Work Sans",sans-serif;font-weight:700;font-size:19px;display:flex;align-items:center;justify-content:center}
.hero-arrow{top:300px}
.hero-curve{left:0;top:600px}

/* What we do */
.section-title{font-family:"Work Sans",sans-serif;font-weight:700;color:var(--ink);text-transform:uppercase}
.what-title{left:0;width:1200px;top:714px;text-align:center;font-size:37px}
.what-intro{left:160px;width:880px;top:784px;text-align:center;font-size:15px;line-height:29px}
.card{top:930px;width:289px;text-align:center}
.card.featured{box-shadow:0 2px 14px rgba(0,0,0,.18);height:420px}
.card-photo{width:289px;height:182px}
.card h3{font-family:"Work Sans",sans-serif;font-weight:700;font-size:18px;color:var(--ink);margin-top:22px;text-transform:uppercase}
.card p{font-size:12px;line-height:24px;margin:12px 8px 0}
.btn-outline{display:inline-flex;align-items:center;justify-content:center;border:2px solid var(--red);border-radius:16px;color:var(--red);font-family:"Work Sans",sans-serif;font-weight:700;text-transform:uppercase}
.card .btn-outline{width:108px;height:28px;font-size:11px;margin-top:20px}

/* Welcome */
.welcome{left:0;top:1482px;width:1200px;height:600px;background:var(--light)}
.welcome-photo{left:138px;top:1578px;width:342px;height:342px;border-radius:50%;border:8px solid #9a9a9a;background:radial-gradient(circle at 45% 60%,#e07a2c 0%,#c9c3b6 45%,#8e9aa3 100%)}
.welcome-kicker{left:538px;top:1572px;font-family:"Work Sans",sans-serif;font-size:36px;color:var(--ink)}
.welcome-title{left:538px;top:1614px;font-size:40px;letter-spacing:1px}
.welcome-text{left:538px;top:1680px;width:525px;font-size:13px;line-height:27.5px}
.welcome-btn{left:540px;top:1866px;width:124px;height:33px;font-size:14px}

/* Newsletter */
.news-bg{left:0;top:2040px;width:1200px;height:320px}
.mail-badge{left:567px;top:1988px;width:66px;height:66px;border-radius:50%;background:var(--dark);border:3px solid var(--white);display:flex;align-items:center;justify-content:center}
.news-title{left:0;width:1200px;top:2124px;text-align:center;font-size:35px;color:var(--white)}
.news-sub{left:0;width:1200px;top:2180px;text-align:center;font-family:"Work Sans",sans-serif;font-size:16px;color:var(--white);letter-spacing:.5px}
.news-form{left:370px;top:2231px;width:460px;height:42px;background:var(--white);border-radius:21px;overflow:hidden}
.news-form span{position:absolute;left:20px;top:13px;font-size:11px;color:#777}
.news-form b{position:absolute;right:0;top:0;width:132px;height:42px;background:var(--red);border-radius:21px;color:var(--white);font-family:"Work Sans",sans-serif;font-size:14px;display:flex;align-items:center;justify-content:center;text-transform:uppercase}

/* Latest news */
.latest-title{left:130px;top:2424px;font-size:28px}
.latest-nav{left:1024px;top:2430px;font-size:16px;color:var(--ink);letter-spacing:6px}
.post-photo{top:2500px;width:175px;height:180px;border-bottom:3px solid var(--red);border-right:3px solid var(--red)}
.post{top:2505px;width:310px}
.post h4{font-family:"Work Sans",sans-serif;font-weight:400;font-size:15px;color:var(--ink);white-space:nowrap}
.post .date{font-size:11px;font-weight:700;color:var(--red);margin-top:14px}
.post p{font-size:11px;line-height:21px;margin-top:10px;width:245px}
.post .more{font-size:12px;color:var(--red);margin-top:14px}

/* Footer */
.footer{left:0;top:2770px;width:1200px;height:393px;background:linear-gradient(180deg,var(--red) 0%,var(--red-dark) 100%)}
.foot-head{top:2832px;font-family:"Work Sans",sans-serif;font-weight:700;font-size:19px;color:var(--white);text-transform:uppercase}
.foot-text{font-size:12px;line-height:21px;color:var(--white)}
.foot-row{display:flex;gap:14px;align-items:flex-start}
.hours{font-family:"Work Sans",sans-serif;font-size:15px;line-height:22px;color:var(--white)}
.links{list-style:none;font-size:12px;line-height:24px;color:var(--white)}
.social{list-style:none;font-size:13px;color:var(--white)}
.social li{display:flex;align-items:center;gap:9px;height:34px}
.social i{width:24px;height:24px;border:1.5px solid var(--white);border-radius:50%;display:inline-block}
.foot-rule{left:0;top:3062px;width:1200px;height:1px;background:rgba(255,255,255,.35)}
.copyright{left:0;width:1200px;top:3104px;text-align:center;font-size:13px;font-weight:600;color:var(--white)}
</style>
</head>
<body>

<!-- Hero -->
<section class="hero abs" role="img" aria-label="Loft office with pendant lamps, desks and large windows">
  <div class="hero-shade abs"></div>
</section>
<div class="brand abs">HIVEDESK</div>
<nav class="nav abs"><span>Home</span><span>Residents</span><span>Our Working Space</span><span>Our Event Space</span><span>Contact</span></nav>
<div class="lang abs">ENGLISH
  <svg width="8" height="6" viewBox="0 0 8 6"><path d="M1 1l3 3 3-3" fill="none" stroke="#fff" stroke-width="1.5"/></svg>
</div>
<h1 class="hero-title abs">HIVEDESK</h1>
<div class="btn-quote abs">GET A QUOTE</div>
<svg class="hero-arrow abs" style="left:104px" width="30" height="66" viewBox="0 0 30 66"><path d="M26 4L4 33l22 29" fill="none" stroke="#fff" stroke-width="2"/></svg>
<svg class="hero-arrow abs" style="left:1066px" width="30" height="66" viewBox="0 0 30 66"><path d="M4 4l22 29L4 62" fill="none" stroke="#fff" stroke-width="2"/></svg>
<svg class="hero-curve abs" width="1200" height="92" viewBox="0 0 1200 92">
  <path d="M0 92V70Q600 -40 1200 70V92Z" fill="#fff"/>
  <path d="M40 98Q600 -30 1160 98" fill="none" stroke="#c4161c" stroke-width="3"/>
</svg>

<!-- What we do -->
<h2 class="section-title what-title abs">What we do</h2>
<p class="what-intro abs">Sed ut perspiciatis unde omnis iste natus error sit voluptatem accusantium doloremque laudantium, totam rem aperiam, eaque ipsa quae ab illo inventore veritatis et quasi architecto beatae vitae dicta sunt explicabo. Nemo enim ipsam voluptatem quia voluptas sit aspernatur aut odit aut fugit, sed quia consequuntur magni dolores eos qui ratione</p>

<article class="card abs" style="left:133px">
  <div class="card-photo" role="img" aria-label="Brick residential house with green lawn" style="background:linear-gradient(180deg,#9bb7c9 0%,#7a4a3a 50%,#4f8a32 100%)"></div>
  <h3>Residents</h3>
  <p>Sed ut perspiciatis unde omnis iste natus error sit voluptatem accusantium doloremque laudantium, totam rem aperiam, eaque ipsa quae ab illo inventore veritatis et quasi architecto</p>
  <span class="btn-outline">Read more</span>
</article>
<article class="card featured abs" style="left:455px">
  <div class="card-photo" role="img" aria-label="Open office with white desks and computer screens" style="background:linear-gradient(180deg,#e6e8ea 0%,#b9bfc4 60%,#8d9399 100%)"></div>
  <h3>Our Working Space</h3>
  <p>Sed ut perspiciatis unde omnis iste natus error sit voluptatem accusantium doloremque laudantium, totam rem aperiam, eaque ipsa quae ab illo inventore veritatis</p>
  <span class="btn-outline">Read more</span>
</article>
<article class="card abs" style="left:778px">
  <div class="card-photo" role="img" aria-label="Event hall with rows of seats and a projection screen" style="background:linear-gradient(180deg,#6f6a62 0%,#3f3b36 55%,#23211f 100%)"></div>
  <h3>Our Event Space</h3>
  <p>Sed ut perspiciatis unde omnis iste natus error sit voluptatem accusantium doloremque laudantium, totam rem aperiam, eaque ipsa quae ab illo inventore veritatis et quasi architecto</p>
  <span class="btn-outline">Read more</span>
</article>

<!-- Welcome -->
<section class="welcome abs"></section>
<div class="welcome-photo abs" role="img" aria-label="Lounge area with orange armchairs in a bright office"></div>
<div class="welcome-kicker abs">welcome to</div>
<h2 class="section-title welcome-title abs">hivedesk</h2>
<p class="welcome-text abs">Sed ut perspiciatis unde omnis iste natus error sit voluptatem accusantium doloremque laudantium, totam rem aperiam, eaque ipsa quae ab illo inventore veritatis et quasi architecto beatae vitae dicta sunt explicabo. Nemo enim ipsam voluptatem quia voluptas sit aspernatur aut odit aut fugit, sed quia consequuntur magni dolores eos qui ratione voluptatem sequi nesciunt. Neque porro quisquam est, qui dolorem ipsum quia dolor sit amet, consectetur, adipisci velit</p>
<span class="btn-outline welcome-btn abs">Read more</span>

<!-- Newsletter -->
<div class="news-bg abs" role="img" aria-label="Dimmed loft office interior" style="background:linear-gradient(180deg,#3b3b3b 0%,#2a2a2a 100%)"></div>
<svg class="abs" style="left:0;top:2010px" width="1200" height="80" viewBox="0 0 1200 80">
  <path d="M0 0H1200V74L600 12L0 74Z" fill="#f1f1f1"/>
  <path d="M0 74L600 12L1200 74" fill="none" stroke="#c4161c" stroke-width="4"/>
</svg>
<div class="mail-badge abs">
  <svg width="28" height="22" viewBox="0 0 28 22"><rect x="1.5" y="1.5" width="25" height="19" rx="3" fill="none" stroke="#fff" stroke-width="2"/><path d="M2 3l12 9 12-9" fill="none" stroke="#fff" stroke-width="2"/></svg>
</div>
<h2 class="section-title news-title abs">Join our newsletter</h2>
<p class="news-sub abs">Stay up to date with the latest news</p>
<div class="news-form abs"><span>Enter Your Email</span><b>Subscribe</b></div>

<!-- Latest news -->
<h2 class="section-title latest-title abs">Latest news</h2>
<div class="latest-nav abs">← →</div>

<div class="post-photo abs" style="left:130px;background:linear-gradient(180deg,#dfe3e6 0%,#9aa3a8 60%,#6f7478 100%)" role="img" aria-label="Glass-walled office interior with plants"></div>
<article class="post abs" style="left:330px">
  <h4>Nulla at diam ornare, aliquam urna</h4>
  <div class="date">MAY 25, 2018</div>
  <p>Nulla at diam ornare, aliquam urna vel, modo urna. Nam id risus a est luctus consectetur quis eget libero. Suspendisse potenti.</p>
  <div class="more">Read More +</div>
</article>

<div class="post-photo abs" style="left:627px;background:linear-gradient(180deg,#8fb6d8 0%,#d8c9a4 55%,#5d9a3a 100%)" role="img" aria-label="Yellow family house with green lawn"></div>
<article class="post abs" style="left:825px">
  <h4>Nulla at diam ornare, aliquam urna</h4>
  <div class="date">MAY 25, 2018</div>
  <p>Nulla at diam ornare, aliquam urna vel, modo urna. Nam id risus a est luctus consectetur quis eget libero. Suspendisse potenti.</p>
  <div class="more">Read More +</div>
</article>

<!-- Footer -->
<footer class="footer abs" role="img" aria-label="Faint red-tinted office interior"></footer>

<h3 class="foot-head abs" style="left:130px">Contact us</h3>
<div class="abs" style="left:130px;top:2880px;width:260px">
  <div class="foot-row foot-text">
    <svg width="18" height="22" viewBox="0 0 18 22"><path d="M9 21s-7-8-7-12a7 7 0 0 1 14 0c0 4-7 12-7 12z" fill="none" stroke="#fff" stroke-width="1.5"/><circle cx="9" cy="9" r="2.5" fill="none" stroke="#fff" stroke-width="1.5"/></svg>
    <span>hivedesk hub<br>Havnegade 12 and Kirkestræde 4,<br>3rd floor 4700 Brovang &nbsp;Denmark</span>
  </div>
  <div class="foot-row foot-text" style="margin-top:12px">
    <svg width="18" height="18" viewBox="0 0 18 18"><path d="M4 1l3 4-2 2c1 2 3 4 5 5l2-2 4 3-2 3C8 16 2 10 1 4z" fill="none" stroke="#fff" stroke-width="1.4"/></svg>
    <span>Phone : (+45) 20 00 41 17</span>
  </div>
  <div class="foot-row foot-text" style="margin-top:10px">
    <svg width="18" height="14" viewBox="0 0 18 14"><rect x="1" y="1" width="16" height="12" fill="none" stroke="#fff" stroke-width="1.4"/><path d="M1 1l8 7 8-7" fill="none" stroke="#fff" stroke-width="1.4"/></svg>
    <span>Email: info@hivedesk.dk</span>
  </div>
</div>

<h3 class="foot-head abs" style="left:412px">Opening hours</h3>
<div class="abs foot-row" style="left:412px;top:2880px">
  <svg width="20" height="20" viewBox="0 0 20 20"><circle cx="10" cy="10" r="8.5" fill="none" stroke="#fff" stroke-width="2"/><path d="M10 5v5h4" fill="none" stroke="#fff" stroke-width="2"/></svg>
  <div class="hours">For residents:<br>24-7. All weekdays.<br><span style="display:block;height:14px"></span>For guests:<br>Monday-Friday: 9:00 - 16:00</div>
</div>

<h3 class="foot-head abs" style="left:740px">Quick links</h3>
<ul class="links abs" style="left:740px;top:2880px">
  <li>Home</li><li>Residents</li><li>Our Working Space</li><li>Our Event Space</li><li>Contact</li>
</ul>

<h3 class="foot-head abs" style="left:957px">Social</h3>
<ul class="social abs" style="left:957px;top:2880px">
  <li><i></i>Facepage</li><li><i></i>Chirper</li><li><i></i>Searchly+</li><li><i></i>vidtube</li>
</ul>

<div class="foot-rule abs"></div>
<p class="copyright abs">Copyright © hivedesk 2018. All rights reserved.</p>

</body>
</html>
```